Webshop for furniture and lamps

We need a design for a web shop with APP that should have two options:
1-Webshop in general which should attract to private customer in general and
2-Website that is meant to attract big customers as hotels and restaurants who would have their own customerize login.

That's the idea behind the shop.

It should be diveded into 4 parts
vintage furniture
rattan set outdoor and indoor
lamps and
wooden wall decor

The name of the shop is loma vereda!

Please kindly make me an offer.

Reason: Dear designers, so far there hasn't been a design that really matched. Look up German web sites like www.glimmerhof-wohnen.de or www.sitzraum77.de... Haven't been convinced by designs! Sorry folks. Please submit some new ones. Kind regards Ned

```html
<!DOCTYPE html>
<html lang="en">
<head>
<meta charset="utf-8">
<title>loma vereda – furniture &amp; lamps</title>
<link href="https://fonts.googleapis.com/css2?family=Open+Sans:wght@400;600;700;800&display=swap" rel="stylesheet">
<style>
:root{
  --teal:#1fb3a6;
  --teal-dark:#17998e;
  --ink:#333333;
  --dark:#2f2f2f;
  --grey:#7a7a7a;
  --light-grey:#b9b9b9;
  --line:#dddddd;
  --taupe:#aaa293;
  --red:#d2102a;
  --orange:#f08a24;
  --cream:#f2efe9;
  --gold:#f2b705;
  --white:#ffffff;
}
*{box-sizing:border-box;margin:0;padding:0}
html,body{width:1200px;height:2851px;overflow:hidden;background:var(--white)}
body{font-family:"Open Sans",Arial,sans-serif;color:var(--ink);position:relative}
.abs{position:absolute}

/* top bar */
.topbar{top:0;left:0;width:1200px;height:45px;background:var(--dark);color:#eee;font-size:13px}
.topbar .welcome-note{position:absolute;left:92px;top:13px}
.topbar .top-links{position:absolute;right:92px;top:13px;display:flex;gap:34px}

/* header */
.header{top:45px;left:0;width:1200px;height:120px}
.brand{position:absolute;left:92px;top:46px;display:flex;align-items:center;gap:14px}
.brand .mark{width:72px;height:38px;background:var(--dark)}
.brand .name{font-size:36px;font-weight:700;color:var(--teal);letter-spacing:0.5px;text-transform:uppercase;line-height:1}
.nav{position:absolute;right:92px;top:52px;display:flex;gap:22px;font-size:12.5px;font-weight:700;color:var(--dark);align-items:center}
.nav .sep{width:1px;height:20px;background:var(--line)}

/* left column */
.left{left:90px;width:298px}
.welcome{top:166px;height:314px;background:var(--teal);color:var(--white);text-align:center}
.welcome h2{font-size:26px;font-weight:800;margin-top:24px}
.welcome .avatar{width:96px;height:96px;border-radius:50%;background:radial-gradient(circle,#f4d9c6,#c98a74);margin:14px auto 12px}
.welcome p{font-size:13.5px;font-weight:600;line-height:18px;padding:0 30px}
.btn-dark{display:inline-block;background:var(--dark);color:var(--white);font-size:13px;font-weight:700;padding:7px 18px;margin-top:12px}

.side-head{height:30px;background:var(--teal);color:var(--white);font-size:13px;font-weight:700;text-transform:uppercase;padding:7px 10px;position:relative}
.side-head .plus{position:absolute;right:0;top:0;width:36px;height:30px;background:var(--dark);color:var(--white);font-size:24px;line-height:28px;text-align:center;font-weight:400}

.category{top:522px}
.category ul{list-style:none;margin-top:12px}
.category li{display:flex;align-items:center;gap:14px;height:31px;font-size:10.5px;font-weight:600;color:#666;text-transform:uppercase;padding-left:20px;border-bottom:1px dashed #e1e1e1}
.category li:first-child{color:var(--teal)}
.category li .box{width:16px;height:16px;background:#a09b91;color:var(--white);font-size:13px;line-height:15px;text-align:center}
.category li:first-child .box{background:var(--teal)}

.why{top:746px}
.why-item{display:flex;gap:12px;padding:22px 0 18px 20px;border-bottom:1px dashed #d6d6d6;height:119px}
.num{width:32px;height:32px;flex:none;background:var(--taupe);color:var(--white);font-weight:700;font-size:15px;text-align:center;line-height:32px}
.num.on{background:var(--teal)}
.why-item h4{font-size:10.5px;color:var(--teal);font-weight:700;text-transform:uppercase}
.why-item .sub{font-size:8.5px;color:var(--light-grey);margin-bottom:7px}
.why-item p{font-size:9.5px;line-height:14px;color:var(--light-grey)}

.blog{top:1392px}
.blog .side-head{padding-right:0}
.tabs{position:absolute;right:0;top:0;display:flex;height:30px}
.tabs span{background:#8f8a80;color:var(--white);font-size:11px;font-weight:700;padding:7px 8px;border-left:1px solid #777}
.tabs span.on{background:var(--dark)}
.post{display:flex;gap:12px;padding:22px 0 10px 20px}
.date{width:32px;flex:none}
.date b{display:block;height:30px;background:var(--teal);color:var(--white);text-align:center;line-height:30px;font-size:15px}
.date i{display:block;height:30px;background:var(--taupe);color:var(--white);text-align:center;line-height:30px;font-size:15px;font-style:normal;font-weight:700}
.post h4{font-size:10.5px;color:var(--teal);font-weight:700;text-transform:uppercase}
.post .sub{font-size:8.5px;color:var(--light-grey);margin-bottom:6px}
.post p{font-size:9.5px;line-height:14px;color:var(--light-grey)}

.ad{top:1700px;height:510px;background:linear-gradient(160deg,#e2c9a0 0%,#c0934f 45%,#7a3f17 100%)}

/* right column */
.right{left:425px;width:680px}
.hero{top:166px;height:314px;background:linear-gradient(120deg,#8c6a4a 0%,#5c4330 35%,#3a2a22 60%,#d9d3c8 100%)}
.hero-copy{position:absolute;left:423px;top:58px;color:var(--white)}
.hero-copy h1{font-size:32px;font-weight:800;line-height:36px;text-transform:uppercase}
.hero-copy p{font-size:12.5px;font-weight:700;line-height:19px;text-transform:uppercase;margin-top:10px}
.btn-teal{display:inline-block;background:var(--teal);color:var(--white);font-size:13px;font-weight:700;padding:7px 15px;margin-top:16px}

.sec-head{height:33px;border-bottom:2px solid #d9d9d9;position:relative}
.sec-head .label{display:inline-block;height:33px;background:var(--teal);color:var(--white);font-size:13px;font-weight:700;text-transform:uppercase;padding:8px 10px}
.arrows{position:absolute;right:0;top:3px;display:flex;gap:2px}
.arrows span{width:26px;height:26px;background:var(--dark);display:flex;align-items:center;justify-content:center}
.viewall{position:absolute;right:0;top:3px;height:27px;background:var(--dark);color:var(--white);font-size:12px;font-weight:700;padding:5px 12px}

.grid{display:grid;grid-template-columns:repeat(3,1fr);column-gap:10px;margin-top:20px}
.card{text-align:center;position:relative;padding-top:40px}
.card.flat{padding-top:22px}
.badge{position:absolute;top:8px;right:36px;width:36px;height:36px;border-radius:50%;background:var(--orange);color:var(--white);font-size:10px;font-weight:800;line-height:36px}
.badge.big{width:44px;height:44px;line-height:44px;font-size:16px;right:auto;left:10px;top:18px}
.badge.big.r{left:auto;right:50px}
.pic{width:160px;height:150px;margin:0 auto;border-radius:4px}
.p1{background:linear-gradient(160deg,#c65a3a,#3f6c7a 60%,#6e4a33)}
.p2{background:linear-gradient(180deg,#e6ddcf 0%,#b58a5a 40%,#5f7a86 100%)}
.p3{background:linear-gradient(170deg,#d9cbb3,#a36b49 55%,#6f9aa0)}
.p4{background:linear-gradient(180deg,#6a6a6a,#2e2e2e 60%,#8a7a66)}
.p5{background:linear-gradient(180deg,#f3dfa9 0%,#d8b066 40%,#b78f55 100%)}
.p6{background:linear-gradient(180deg,#b8875d,#8b5a38 60%,#c9a27a)}
.p7{background:linear-gradient(170deg,#6d3a22,#a06a46 60%,#3d2a1e)}
.p8{background:linear-gradient(180deg,#8a4e2a,#c38a4e 50%,#5a2e18)}
.stars{font-size:11px;letter-spacing:2px;color:var(--gold);margin-top:14px}
.stars .off{color:#cfcfcf}
.card h5{font-size:10.5px;font-weight:800;color:var(--dark);margin-top:6px;text-transform:uppercase}
.card .desc{font-size:9.5px;color:#777;line-height:13px;margin-top:3px}
.price{font-size:15px;font-weight:700;color:var(--red);margin-top:5px}
.buy{display:inline-flex;margin-top:12px;height:24px}
.buy .txt{background:var(--taupe);color:var(--white);font-size:9px;font-weight:700;padding:0 10px;line-height:24px}
.buy .cart{width:26px;background:var(--teal);display:flex;align-items:center;justify-content:center}

.new{top:522px}
.best{top:936px}
.featured{top:1350px}
.featured .grid{row-gap:48px}
.brands{top:2110px}
.brand-row{display:flex;justify-content:space-between;align-items:center;margin-top:34px;padding:0 12px}
.brand-row span{font-size:20px;font-weight:700;color:#555;letter-spacing:0.5px}

/* tweet band */
.tweet{top:2293px;left:0;width:1200px;height:90px;background:var(--cream);display:flex;align-items:center;justify-content:center;gap:14px;font-size:13.5px;color:#555}
.tweet .dot{width:22px;height:22px;border-radius:50%;background:var(--teal)}
.tweet b{color:var(--teal-dark);font-weight:700}

/* footer */
.footer{top:2383px;left:0;width:1200px;height:195px;background:var(--dark);color:#cfcfcf}
.fcols{position:absolute;left:112px;top:26px;display:flex;gap:0}
.fcol{width:206px}
.fcol h6{font-size:12px;font-weight:700;color:var(--white);text-transform:uppercase;margin-bottom:14px}
.fcol p{font-size:9.5px;line-height:14px;width:150px}
.more{display:flex;align-items:center;gap:8px;font-size:9.5px;color:var(--white);margin-top:22px}
.more i{width:10px;height:10px;border-radius:50%;background:var(--teal);display:block}
.signup{position:absolute;left:950px;top:26px;width:220px}
.signup h6{font-size:12px;font-weight:700;color:var(--white);text-transform:uppercase;margin-bottom:14px}
.signup p{font-size:10px;line-height:15px}
.signup .form{display:flex;margin-top:18px}
.signup .field{width:128px;height:30px;background:var(--white);color:#999;font-size:8.5px;line-height:30px;padding-left:8px}
.signup .go{width:50px;height:30px;background:var(--teal);color:var(--white);font-size:10px;line-height:30px;text-align:center}

.bar{top:2578px;left:0;width:1200px;height:59px;background:var(--teal);color:var(--white);font-size:12px}
.bar .loc{position:absolute;left:112px;top:21px;display:flex;gap:34px}
.bar .links{position:absolute;left:460px;top:21px;display:flex;gap:22px}
.bar .social{position:absolute;right:92px;top:16px;display:flex;gap:8px}
.bar .social span{width:27px;height:27px;display:block}

.legal{top:2665px;left:0;width:1200px;text-align:center;font-size:11px;line-height:17px;color:#444}
.legal a{color:var(--teal-dark);text-decoration:none}
.seals{top:2752px;left:0;width:1200px;display:flex;justify-content:center;align-items:center;gap:24px}
.seals span{display:block;background:#d7d7d7;border-radius:4px;height:28px}
</style>
</head>
<body>

<div class="abs topbar">
  <div class="welcome-note">Mirela, welcome to our online store!</div>
  <div class="top-links"><span>Login</span><span>&#9679; My Account &#8964;</span><span>0 item</span><span>Checkout</span></div>
</div>

<header class="abs header">
  <div class="brand"><span class="mark"></span><span class="name">loma vereda</span></div>
  <nav class="nav">
    <span>HOME</span><span>SHOP BY BRAND</span><span>TOP SELLERS</span><span>CLEARANCE</span><span>HELP CENTER</span><span>MY FAVORITES</span><span class="sep"></span>
    <svg width="14" height="14" viewBox="0 0 14 14"><circle cx="6" cy="6" r="4.5" fill="none" stroke="#2f2f2f" stroke-width="1.8"/><line x1="9.3" y1="9.3" x2="13" y2="13" stroke="#2f2f2f" stroke-width="1.8"/></svg>
  </nav>
</header>

<section class="abs left welcome">
  <h2>HI MIRELA!</h2>
  <div class="avatar" role="img" aria-label="Customer profile portrait"></div>
  <p>accusantium laudantium unde perspiciatis ipsam sed</p>
  <span class="btn-dark">Learn more</span>
</section>

<section class="abs left category">
  <div class="side-head">Shop by category<span class="plus">+</span></div>
  <ul>
    <li><span class="box">+</span>Vintage furniture</li>
    <li><span class="box">+</span>Rattan set outdoor and indoor</li>
    <li><span class="box">+</span>Lamps and</li>
    <li><span class="box">+</span>Wooden wall decor</li>
  </ul>
</section>

<section class="abs left why">
  <div class="side-head">Why you choose us<span class="plus">+</span></div>
  <div class="why-item"><span class="num on">01</span><div><h4>Perspiciatis ipsam</h4><div class="sub">Voluptatum, Totam</div><p>Enim accusantium laudantium laudantium perspiciatis ipsam sed doloremque ipsam, totam unde</p></div></div>
  <div class="why-item"><span class="num">02</span><div><h4>Perspiciatis ipsam</h4><div class="sub">Voluptatum, Totam</div><p>Enim accusantium laudantium laudantium perspiciatis ipsam sed doloremque ipsam, totam unde</p></div></div>
  <div class="why-item"><span class="num">03</span><div><h4>Perspiciatis ipsam</h4><div class="sub">Voluptatum, Totam</div><p>Enim accusantium laudantium laudantium perspiciatis ipsam sed doloremque ipsam, totam unde</p></div></div>
  <div class="why-item"><span class="num">04</span><div><h4>Perspiciatis ipsam</h4><div class="sub">Voluptatum, Totam</div><p>Enim accusantium laudantium laudantium perspiciatis ipsam sed doloremque ipsam, totam unde</p></div></div>
  <div class="why-item"><span class="num">05</span><div><h4>Perspiciatis ipsam</h4><div class="sub">Voluptatum, Totam</div><p>Enim accusantium laudantium laudantium perspiciatis ipsam sed doloremque ipsam</p></div></div>
</section>

<section class="abs left blog">
  <div class="side-head">News from blog<div class="tabs"><span>MENU 2</span><span class="on">MENU 3</span></div></div>
  <div class="post"><div class="date"><b>10</b><i>11</i></div><div><h4>Varitatis beatae vos</h4><div class="sub">Voluptatum, Totam</div><p>Accusantium laudantium laudantium perspiciatis ipsam sed doloremque ipsam totam unde accusantium</p></div></div>
  <div class="post"><div class="date"><b>10</b><i>11</i></div><div><h4>Totam unde</h4><div class="sub">Voluptatum, Totam</div><p>Accusantium laudantium laudantium perspiciatis ipsam sed doloremque ipsam totam unde accusantium</p></div></div>
</section>

<div class="abs left ad" role="img" aria-label="Advertisement for a luxury upholstered armchair by Calmyra"></div>

<section class="abs right hero" role="img" aria-label="Bedroom interior with upholstered bed and stone wall">
  <div class="hero-copy">
    <h1>Accusanti<br>laudantium</h1>
    <p>Perspiciatis dolore totam<br>unde unde et aut illo aut</p>
    <span class="btn-teal">pre-order now</span>
  </div>
</section>

<section class="abs right new">
  <div class="sec-head"><span class="label">New products of the week</span>
    <div class="arrows"><span><svg width="8" height="10"><path d="M6 1 2 5l4 4" stroke="#fff" stroke-width="2" fill="none"/></svg></span><span><svg width="8" height="10"><path d="M2 1l4 4-4 4" stroke="#fff" stroke-width="2" fill="none"/></svg></span></div></div>
  <div class="grid">
    <div class="card"><span class="badge">NEW</span><div class="pic p1" role="img" aria-label="Painted vintage chest of drawers"></div><div class="stars">★★★★<span class="off">★</span></div><h5>Rem ipsam quas</h5><p class="desc">Enim accusantium laudantium<br>perspiciatis doloremque</p><div class="price">$ 987.00</div><div class="buy"><span class="txt">BUY NOW</span><span class="cart"><svg width="14" height="12"><path d="M1 1h2l2 7h7l1-5H4" stroke="#fff" stroke-width="1.5" fill="none"/><circle cx="6" cy="10.5" r="1" fill="#fff"/><circle cx="11" cy="10.5" r="1" fill="#fff"/></svg></span></div></div>
    <div class="card"><span class="badge">NEW</span><div class="pic p2" role="img" aria-label="Reclaimed wood dining table"></div><div class="stars">★★★★<span class="off">★</span></div><h5>Rem ipsam quas</h5><p class="desc">Enim accusantium laudantium<br>perspiciatis doloremque</p><div class="price">$ 987.00</div><div class="buy"><span class="txt">BUY NOW</span><span class="cart"><svg width="14" height="12"><path d="M1 1h2l2 7h7l1-5H4" stroke="#fff" stroke-width="1.5" fill="none"/><circle cx="6" cy="10.5" r="1" fill="#fff"/><circle cx="11" cy="10.5" r="1" fill="#fff"/></svg></span></div></div>
    <div class="card"><span class="badge">NEW</span><div class="pic p3" role="img" aria-label="Distressed wooden sideboard"></div><div class="stars">★★★★<span class="off">★</span></div><h5>Rem ipsam quas</h5><p class="desc">Enim accusantium laudantium<br>perspiciatis doloremque</p><div class="price">$ 987.00</div><div class="buy"><span class="txt">BUY NOW</span><span class="cart"><svg width="14" height="12"><path d="M1 1h2l2 7h7l1-5H4" stroke="#fff" stroke-width="1.5" fill="none"/><circle cx="6" cy="10.5" r="1" fill="#fff"/><circle cx="11" cy="10.5" r="1" fill="#fff"/></svg></span></div></div>
  </div>
</section>

<section class="abs right best">
  <div class="sec-head"><span class="label">Bestseller products</span>
    <div class="arrows"><span><svg width="8" height="10"><path d="M6 1 2 5l4 4" stroke="#fff" stroke-width="2" fill="none"/></svg></span><span><svg width="8" height="10"><path d="M2 1l4 4-4 4" stroke="#fff" stroke-width="2" fill="none"/></svg></span></div></div>
  <div class="grid">
    <div class="card"><span class="badge big r">50.</span><div class="pic p4" role="img" aria-label="Dark rattan outdoor dining set"></div><div class="stars">★★★★<span class="off">★</span></div><h5>Rem ipsam quas</h5><p class="desc">Enim accusantium laudantium<br>perspiciatis doloremque</p><div class="price">$ 987.00</div><div class="buy"><span class="txt">BUY NOW</span><span class="cart"><svg width="14" height="12"><path d="M1 1h2l2 7h7l1-5H4" stroke="#fff" stroke-width="1.5" fill="none"/><circle cx="6" cy="10.5" r="1" fill="#fff"/><circle cx="11" cy="10.5" r="1" fill="#fff"/></svg></span></div></div>
    <div class="card"><span class="badge big">20.</span><div class="pic p5" role="img" aria-label="Brass floor lamp with cream shade"></div><div class="stars">★★★★<span class="off">★</span></div><h5>Rem ipsam quas</h5><p class="desc">Enim accusantium laudantium<br>perspiciatis doloremque</p><div class="price">$ 987.00</div><div class="buy"><span class="txt">BUY NOW</span><span class="cart"><svg width="14" height="12"><path d="M1 1h2l2 7h7l1-5H4" stroke="#fff" stroke-width="1.5" fill="none"/><circle cx="6" cy="10.5" r="1" fill="#fff"/><circle cx="11" cy="10.5" r="1" fill="#fff"/></svg></span></div></div>
    <div class="card"><div class="pic p6" role="img" aria-label="Round rattan dining set"></div><div class="stars">★★★★<span class="off">★</span></div><h5>Rem ipsam quas</h5><p class="desc">Enim accusantium laudantium<br>perspiciatis doloremque</p><div class="price">$ 987.00</div><div class="buy"><span class="txt">BUY NOW</span><span class="cart"><svg width="14" height="12"><path d="M1 1h2l2 7h7l1-5H4" stroke="#fff" stroke-width="1.5" fill="none"/><circle cx="6" cy="10.5" r="1" fill="#fff"/><circle cx="11" cy="10.5" r="1" fill="#fff"/></svg></span></div></div>
  </div>
</section>

<section class="abs right featured">
  <div class="sec-head"><span class="label">Featured products</span><span class="viewall">view all</span></div>
  <div class="grid">
    <div class="card flat"><div class="pic p7" role="img" aria-label="Vintage wooden cabinet"></div><div class="stars">★★★★<span class="off">★</span></div><h5>Rem ipsam quas</h5><p class="desc">Enim accusantium laudantium<br>perspiciatis doloremque</p><div class="price">$ 987.00</div><div class="buy"><span class="txt">BUY NOW</span><span class="cart"><svg width="14" height="12"><path d="M1 1h2l2 7h7l1-5H4" stroke="#fff" stroke-width="1.5" fill="none"/><circle cx="6" cy="10.5" r="1" fill="#fff"/><circle cx="11" cy="10.5" r="1" fill="#fff"/></svg></span></div></div>
    <div class="card flat"><div class="pic p1" role="img" aria-label="Painted vintage chest of drawers"></div><div class="stars">★★★★<span class="off">★</span></div><h5>Rem ipsam quas</h5><p class="desc">Enim accusantium laudantium<br>perspiciatis doloremque</p><div class="price">$ 987.00</div><div class="buy"><span class="txt">BUY NOW</span><span class="cart"><svg width="14" height="12"><path d="M1 1h2l2 7h7l1-5H4" stroke="#fff" stroke-width="1.5" fill="none"/><circle cx="6" cy="10.5" r="1" fill="#fff"/><circle cx="11" cy="10.5" r="1" fill="#fff"/></svg></span></div></div>
    <div class="card flat"><div class="pic p8" role="img" aria-label="Tall wooden glass-front cabinet"></div><div class="stars">★★★★<span class="off">★</span></div><h5>Rem ipsam quas</h5><p class="desc">Enim accusantium laudantium<br>perspiciatis doloremque</p><div class="price">$ 987.00</div><div class="buy"><span class="txt">BUY NOW</span><span class="cart"><svg width="14" height="12"><path d="M1 1h2l2 7h7l1-5H4" stroke="#fff" stroke-width="1.5" fill="none"/><circle cx="6" cy="10.5" r="1" fill="#fff"/><circle cx="11" cy="10.5" r="1" fill="#fff"/></svg></span></div></div>
    <div class="card flat"><div class="pic p6" role="img" aria-label="Round rattan dining set"></div><div class="stars">★★★★<span class="off">★</span></div><h5>Rem ipsam quas</h5><p class="desc">Enim accusantium laudantium<br>perspiciatis doloremque</p><div class="price">$ 987.00</div><div class="buy"><span class="txt">BUY NOW</span><span class="cart"><svg width="14" height="12"><path d="M1 1h2l2 7h7l1-5H4" stroke="#fff" stroke-width="1.5" fill="none"/><circle cx="6" cy="10.5" r="1" fill="#fff"/><circle cx="11" cy="10.5" r="1" fill="#fff"/></svg></span></div></div>
    <div class="card flat"><div class="pic p3" role="img" aria-label="Distressed wooden sideboard"></div><div class="stars">★★★★<span class="off">★</span></div><h5>Rem ipsam quas</h5><p class="desc">Enim accusantium laudantium<br>perspiciatis doloremque</p><div class="price">$ 987.00</div><div class="buy"><span class="txt">BUY NOW</span><span class="cart"><svg width="14" height="12"><path d="M1 1h2l2 7h7l1-5H4" stroke="#fff" stroke-width="1.5" fill="none"/><circle cx="6" cy="10.5" r="1" fill="#fff"/><circle cx="11" cy="10.5" r="1" fill="#fff"/></svg></span></div></div>
    <div class="card flat"><div class="pic p4" role="img" aria-label="Dark rattan outdoor dining set"></div><div class="stars">★★★★<span class="off">★</span></div><h5>Rem ipsam quas</h5><p class="desc">Enim accusantium laudantium<br>perspiciatis doloremque</p><div class="price">$ 987.00</div><div class="buy"><span class="txt">BUY NOW</span><span class="cart"><svg width="14" height="12"><path d="M1 1h2l2 7h7l1-5H4" stroke="#fff" stroke-width="1.5" fill="none"/><circle cx="6" cy="10.5" r="1" fill="#fff"/><circle cx="11" cy="10.5" r="1" fill="#fff"/></svg></span></div></div>
  </div>
</section>

<section class="abs right brands">
  <div class="sec-head"><span class="label">Search by brand</span>
    <div class="arrows"><span><svg width="8" height="10"><path d="M6 1 2 5l4 4" stroke="#fff" stroke-width="2" fill="none"/></svg></span><span><svg width="8" height="10"><path d="M2 1l4 4-4 4" stroke="#fff" stroke-width="2" fill="none"/></svg></span></div></div>
  <div class="brand-row"><span>Brivanto</span><span>Quelmar</span><span>Tessivo</span><span>Norvique</span><span>Zanterra</span></div>
</section>

<section class="abs tweet">
  <span class="dot"></span>
  <span>“I have never met a designer who was retained to keep things the same as they were.” - <b>Tomas Reyne http://lnk.to/rQ4xZ #KEEPMOVING</b></span>
</section>

<footer class="abs footer">
  <div class="fcols">
    <div class="fcol"><h6>Who we are?</h6><p>Fugit illo omnis explicabo ipsa, nemo quam quasi voluptas dolo perspiciatis beatae magni architecto</p><div class="more">Read more <i></i></div></div>
    <div class="fcol"><h6>What we sell?</h6><p>Omnis explicabo<br>Nemo ipsam quasi<br>Voluptatem dolo<br>Beatae magni archite<br>Odit nemo ipsam quasi</p><div class="more">Read more <i></i></div></div>
    <div class="fcol"><h6>Shipping</h6><p>Fugit illo omnis explicabo ipsa, nemo quam quasi voluptas dolo perspiciatis beatae magni architecto</p><div class="more">Read more <i></i></div></div>
    <div class="fcol"><h6>Track your order</h6><p>Omnis explicabo<br>Nemo ipsam quasi<br>Voluptatem dolo<br>Beatae magni archite<br>Odit nemo ipsam quasi</p><div class="more">Read more <i></i></div></div>
  </div>
  <div class="signup"><h6>Sign up for special deals!</h6><p>Get exclusive access to expert tips, special offers and coupons.</p><div class="form"><span class="field">enter your email address</span><span class="go">Sign Up</span></div></div>
</footer>

<div class="abs bar">
  <div class="loc"><span>United States - English &#8964;</span><span>Currency:USD &#8964;</span></div>
  <div class="links"><span>Home</span><span>About Us</span><span>Privacy Policy</span><span>Contact Us</span></div>
  <div class="social"><span style="background:#3b5a9a"></span><span style="background:#2fa7d8"></span><span style="background:#d5412e"></span><span style="background:#7a7a7a"></span><span style="background:#1d7ab5"></span><span style="background:#c8232c"></span></div>
</div>

<div class="abs legal">
  Use of this Site is subject to express terms of use. By using this site, you signify that you agree<br>
  to be bound by these <a>Universal Terms of Service</a>, <a>Legal</a>, <a>Privacy Policy</a><br>
  Copyright © 2014 Your Company. All Rights Reserved.
</div>

<div class="abs seals">
  <span style="width:80px"></span><span style="width:60px"></span><span style="width:96px"></span><span style="width:52px"></span><span style="width:40px"></span><span style="width:56px"></span><span style="width:126px"></span>
</div>

</body>
</html>
```